Business Card Design for Occupational Medicine Start Up Company

We need to design a professional business card. We are a healthcare company providing occupational medicine services to blue collar industries. We are professional, efficient and high quality service providers.

Target Market(s)

Blue Collar Industry: Shipbuilding, Ports, Trucking Companies; The Executives and Safety Officers for these companies

Industry/Entity Type

Healthcare

Contact Information for Business Card

Logo, Name, Title, Email, Phone

Other font styles liked:
• Please match our Brand Guide

Requirements
Must have
• Our Company Colors and Logo

```html
<!DOCTYPE html>
<html lang="en">
<head>
<meta charset="utf-8">
<title>Crewline Health – Business Card</title>
<link href="https://fonts.googleapis.com/css2?family=Arimo:wght@400;700&family=Montserrat:wght@700&display=swap" rel="stylesheet">
<style>
  :root {
    --page: #e9eaee;
    --navy: #252d7a;
    --royal: #2a2fa0;
    --sky: #1ea3dc;
    --amber: #f5b14c;
    --ink: #4a4a4a;
    --white: #ffffff;
  }
  * { box-sizing: border-box; margin: 0; padding: 0; }
  html, body { width: 1200px; height: 800px; overflow: hidden; }
  body {
    background: var(--page);
    font-family: "Arimo", Arial, sans-serif;
    display: flex;
    align-items: center;
    justify-content: center;
    gap: 40px;
  }
  .card {
    width: 540px;
    height: 309px;
    position: relative;
    overflow: hidden;
    box-shadow: 0 6px 18px rgba(0,0,0,.18);
  }
  /* Back side */
  .card--back { background: var(--royal); }
  .card--back .pattern {
    position: absolute; inset: 0;
    background: linear-gradient(120deg, #3a40d8 0%, #2a2fa0 45%, #1d2170 100%);
  }
  .card--back .brand-mark {
    position: absolute;
    right: 62px; top: 178px;
    color: var(--white);
    font-family: "Montserrat", Arial, sans-serif;
    font-weight: 700;
    font-size: 15px;
    letter-spacing: .04em;
  }
  /* Front side */
  .card--front { background: var(--white); }
  .brand {
    position: absolute;
    left: 40px; top: 132px;
    width: 200px;
    text-align: center;
    font-family: "Montserrat", Arial, sans-serif;
    font-weight: 700;
    font-size: 22px;
    line-height: 1.1;
    color: var(--navy);
    letter-spacing: .02em;
  }
  .divider {
    position: absolute;
    left: 262px; top: 78px;
    width: 1.5px; height: 150px;
    background: var(--navy);
  }
  .contact {
    position: absolute;
    left: 286px; top: 76px;
    color: var(--ink);
    font-size: 12px;
    line-height: 1.35;
  }
  .contact .name { color: var(--navy); font-weight: 700; font-size: 18px; line-height: 1.2; }
  .contact .title { color: var(--sky); font-size: 13px; margin-bottom: 4px; }
  .contact .address { margin-bottom: 6px; }
  .contact ul { list-style: none; }
  .contact li { display: flex; align-items: center; gap: 7px; }
  .contact svg { width: 10px; height: 10px; fill: var(--sky); flex: none; }
  .bands { position: absolute; left: 0; right: 0; bottom: 0; height: 9px; display: flex; }
  .band--sky { background: var(--sky); flex: 40; }
  .band--navy { background: var(--navy); flex: 33; }
  .band--amber { background: var(--amber); flex: 27; }
</style>
</head>
<body>
  <section class="card card--back" aria-label="Card back">
    <div class="pattern" role="img" aria-label="Repeating embossed brand pattern in deep blue tones"></div>
    <span class="brand-mark">Crewline Health</span>
  </section>

  <section class="card card--front" aria-label="Card front">
    <div class="brand">CREWLINE HEALTH</div>
    <div class="divider"></div>
    <div class="contact">
      <p class="name">Daniel Harper</p>
      <p class="title">President</p>
      <p class="address">2214 Dockside Way<br>Kelby Bay, Alaska 99610</p>
      <ul>
        <li><svg viewBox="0 0 10 10"><path d="M2 0.5 L3.8 2.6 3 3.8 Q4 6 6.2 7 L7.4 6.2 9.5 8 8.3 9.5 Q4.5 9.5 1.8 6.6 0.4 4.5 0.5 1.7Z"/></svg>555-014-2290</li>
        <li><svg viewBox="0 0 10 10"><path d="M2.5 0h5v10h-5z M3.3 1v7h3.4v-7z"/></svg>555-017-4631</li>
        <li><svg viewBox="0 0 10 10"><path d="M2.5 0h5v3h-5z M0.5 3.5h9v4h-2v2.5h-5v-2.5h-2z"/></svg>555-019-8847</li>
        <li><svg viewBox="0 0 10 10"><path d="M0 2h10v6h-10z M0.5 2.3 5 5.5 9.5 2.3" stroke="#fff" stroke-width=".8"/></svg>info@crewlinehealth.com</li>
        <li><svg viewBox="0 0 10 10"><circle cx="5" cy="5" r="5"/></svg>crewlinehealth.com</li>
      </ul>
    </div>
    <div class="bands">
      <span class="band--sky"></span>
      <span class="band--navy"></span>
      <span class="band--amber"></span>
    </div>
  </section>
</body>
</html>
```